New Electrical Business Card Design

I would like a new design for my business cards.
i would like the same logo and font but new design
Please see attached files for front and back design.
large image can be used for graphics.
I would like the instagram link incorporated to back of card.
website site address needs to be changed to www.kestrelhillelectrical.au
everything else stays as is

```html
<!DOCTYPE html>
<html lang="en">
<head>
<meta charset="utf-8">
<title>Kestrel Hill Electrical &amp; Data – Business Card</title>
<link rel="stylesheet" href="https://fonts.googleapis.com/css2?family=Poppins:wght@400;700&family=Oswald:wght@700&display=swap">
<style>
  :root {
    --bg: #2b2b2b;
    --card: #ececec;
    --card-light: #f3f3f3;
    --ink: #111111;
    --grey: #6d6d6f;
    --green: #0f7a3a;
    --band: #050505;
    --divider: #3aa6b9;
    --white: #ffffff;
  }
  * { box-sizing: border-box; margin: 0; padding: 0; }
  html, body { width: 1200px; height: 1138px; overflow: hidden; }
  body { background: var(--bg); font-family: "Poppins", sans-serif; position: relative; }

  .card {
    position: absolute;
    left: 273px;
    width: 621px;
    height: 376px;
    border-radius: 16px;
    background: linear-gradient(160deg, var(--card-light), var(--card));
    overflow: hidden;
  }
  .card--front { top: 184px; }
  .card--back { top: 606px; }

  /* Front */
  .front-brand {
    position: absolute; left: 0; right: 0; top: 130px;
    text-align: center; color: var(--ink); font-weight: 700;
  }
  .front-brand .brand-name { font-size: 56px; line-height: 1; letter-spacing: 1px; }
  .front-brand .brand-sub { font-size: 20px; letter-spacing: 13px; margin-top: 10px; padding-left: 13px; }
  .services {
    position: absolute; left: 0; right: 0; top: 227px;
    text-align: center; font-size: 16px; color: var(--ink);
  }
  .front-band { position: absolute; left: 0; right: 0; bottom: 0; height: 12px; background: var(--green); }

  /* Back */
  .back-brand {
    position: absolute; left: 40px; width: 265px; top: 134px;
    text-align: center; color: var(--ink); font-weight: 700;
  }
  .back-brand .brand-name { font-size: 30px; line-height: 1; }
  .back-brand .brand-sub { font-size: 11px; letter-spacing: 7px; margin-top: 6px; padding-left: 7px; }
  .divider { position: absolute; left: 306px; top: 82px; width: 1px; height: 176px; background: var(--divider); }
  .person {
    position: absolute; left: 341px; top: 104px;
    font-family: "Oswald", sans-serif; font-weight: 700; font-size: 21px; letter-spacing: .3px;
  }
  .person .first { color: var(--green); }
  .person .last { color: var(--ink); }
  .contacts { position: absolute; left: 340px; top: 144px; list-style: none; }
  .contacts li { display: flex; align-items: center; height: 22.5px; font-size: 15px; color: #333; }
  .contacts svg { width: 15px; height: 15px; margin-right: 11px; flex: none; }
  .social-dot { width: 13px; height: 13px; border-radius: 3px; background: var(--green); margin: 0 12px 0 1px; flex: none; }
  .back-band {
    position: absolute; left: 0; right: 0; bottom: 0; height: 52px; background: var(--band);
    display: flex; align-items: center; justify-content: center; gap: 40px;
    color: var(--white); font-size: 15px;
  }
  .back-band .rule { width: 50px; height: 2px; background: linear-gradient(90deg, transparent, var(--green), transparent); }
</style>
</head>
<body>
  <section class="card card--front">
    <div class="front-brand">
      <div class="brand-name">KESTREL HILL</div>
      <div class="brand-sub">ELECTRICAL &amp; DATA</div>
    </div>
    <p class="services">Residential &nbsp;|&nbsp; Commercial &nbsp;|&nbsp; Industrial &nbsp;|&nbsp; 24hr Service</p>
    <div class="front-band"></div>
  </section>

  <section class="card card--back">
    <div class="back-brand">
      <div class="brand-name">KESTREL HILL</div>
      <div class="brand-sub">ELECTRICAL &amp; DATA</div>
    </div>
    <div class="divider"></div>
    <h1 class="person"><span class="first">DANIEL</span> <span class="last">MARCHETTI</span></h1>
    <ul class="contacts">
      <li>
        <svg viewBox="0 0 16 16" fill="none" stroke="#0f7a3a" stroke-width="1.4"><circle cx="8" cy="8" r="6.8"/><path d="M5.6 4.8c.5-.4 1-.3 1.2.2l.5 1.1c.1.3 0 .6-.3.8l-.4.3c.4 1 1.2 1.8 2.2 2.2l.3-.4c.2-.3.5-.4.8-.3l1.1.5c.5.2.6.7.2 1.2-.6.7-1.6.8-2.6.2-1.4-.8-2.5-1.9-3.3-3.3-.6-1-.5-2 .3-2.5z" fill="#0f7a3a" stroke="none"/></svg>
        0412 738 905
      </li>
      <li>
        <svg viewBox="0 0 16 16" fill="none" stroke="#0f7a3a" stroke-width="1.4"><rect x="1.5" y="3.5" width="13" height="9" rx="1"/><path d="M1.8 4l6.2 5 6.2-5"/></svg>
        info@kestrelhillelectrical.au
      </li>
      <li>
        <svg viewBox="0 0 16 16" fill="none" stroke="#0f7a3a" stroke-width="1.2"><circle cx="8" cy="8" r="6.5"/><ellipse cx="8" cy="8" rx="2.8" ry="6.5"/><path d="M1.5 8h13M2.5 4.8h11M2.5 11.2h11"/></svg>
        www.kestrelhillelectrical.au
      </li>
      <li>
        <span class="social-dot"></span>
        kestrel.hill.electrical
      </li>
    </ul>
    <div class="back-band">
      <span class="rule"></span>
      <span>ABN: 62 718 204 519 &nbsp;|&nbsp; LIC No.: 481630C</span>
      <span class="rule"></span>
    </div>
  </section>
</body>
</html>
```